MRT Property - Business Cards

Looking for a business card & general letterhead, signage etc design for our new logo.

Colours:
000a20
0056a2
00b5ef
0088ce
68cef2

Fonts:
Poppins
Karla

Please keep look and feel of new brand - example in the zip package I sent.

```html
<!DOCTYPE html>
<html lang="en">
<head>
<meta charset="utf-8">
<title>MRT Property – Business Card</title>
<link href="https://fonts.googleapis.com/css2?family=Poppins:wght@300;400;600;700&display=swap" rel="stylesheet">
<style>
  :root {
    --ink: #000a20;
    --brand-blue: #0056a2;
    --brand-cyan: #00b5ef;
    --brand-mid: #0088ce;
    --brand-light: #68cef2;
    --card-face: #eef1f4;
    --page-bg: #d9dde2;
    --white: #ffffff;
  }
  * { margin: 0; padding: 0; box-sizing: border-box; }
  html, body {
    width: 1200px;
    height: 887px;
    overflow: hidden;
    background: var(--page-bg);
    font-family: "Poppins", sans-serif;
  }
  .business-card {
    position: absolute;
    left: 100px;
    top: 168px;
    width: 1000px;
    height: 550px;
    background: var(--card-face);
    border-radius: 26px;
    overflow: hidden;
    box-shadow: 0 10px 30px rgba(0, 10, 32, 0.12);
  }
  .brand-lockup {
    position: absolute;
    top: 108px;
    left: 0;
    width: 100%;
    display: flex;
    justify-content: center;
    align-items: center;
    gap: 22px;
  }
  .brand-dot {
    width: 58px;
    height: 58px;
    border-radius: 50%;
    background: var(--brand-cyan);
  }
  .brand-name {
    font-weight: 600;
    font-size: 66px;
    line-height: 1;
    color: var(--brand-blue);
    letter-spacing: 1px;
  }
  .contact-band {
    position: absolute;
    top: 284px;
    left: 0;
    width: 100%;
    height: 127px;
    background: linear-gradient(90deg, var(--brand-mid) 0%, var(--brand-blue) 55%, var(--brand-blue) 100%);
  }
  .person {
    position: absolute;
    right: 600px;
    top: 24px;
    text-align: right;
  }
  .person-name {
    font-weight: 700;
    font-size: 40px;
    line-height: 1.05;
    color: var(--brand-light);
    letter-spacing: 1px;
    text-transform: uppercase;
  }
  .person-role {
    font-weight: 300;
    font-size: 22px;
    color: var(--white);
    margin-top: 4px;
  }
  .contact-list {
    position: absolute;
    left: 612px;
    top: 14px;
    list-style: none;
  }
  .contact-item {
    display: flex;
    align-items: center;
    gap: 6px;
    font-weight: 300;
    font-size: 23px;
    line-height: 31px;
    color: var(--white);
  }
  .contact-icon {
    width: 17px;
    height: 17px;
    flex: none;
  }
  .address {
    position: absolute;
    top: 458px;
    left: 0;
    width: 100%;
    text-align: center;
    font-weight: 400;
    font-size: 22px;
    color: var(--ink);
  }
</style>
</head>
<body>
  <div class="business-card">
    <div class="brand-lockup">
      <span class="brand-dot"></span>
      <span class="brand-name">MRT Property</span>
    </div>

    <div class="contact-band">
      <div class="person">
        <div class="person-name">Dana Whitfield</div>
        <div class="person-role">Founder &amp; Principal</div>
      </div>

      <ul class="contact-list">
        <li class="contact-item">
          <svg class="contact-icon" viewBox="0 0 24 24" fill="none" stroke="#00b5ef" stroke-width="2"><path d="M5 3h4l2 5-3 2a12 12 0 0 0 6 6l2-3 5 2v4a2 2 0 0 1-2 2A17 17 0 0 1 3 5a2 2 0 0 1 2-2z"/></svg>
          +1- 415-555-0148
        </li>
        <li class="contact-item">
          <svg class="contact-icon" viewBox="0 0 24 24" fill="none" stroke="#00b5ef" stroke-width="2"><rect x="3" y="5" width="18" height="14" rx="1"/><path d="M3 6l9 7 9-7"/></svg>
          info@mrtproperty.com
        </li>
        <li class="contact-item">
          <svg class="contact-icon" viewBox="0 0 24 24" fill="none" stroke="#00b5ef" stroke-width="2"><circle cx="12" cy="12" r="9"/><path d="M3 12h18M12 3c3 3 3 15 0 18M12 3c-3 3-3 15 0 18"/></svg>
          www.mrtproperty.com
        </li>
      </ul>
    </div>

    <p class="address">2140 West 85th Street #12, Suite Lenexa Park</p>
  </div>
</body>
</html>
```